Growing the Ironclad Young Contender:
A Family Playbook for Nurturing Bold, Grounded, and Resilient Daughters at Games and Beyond.
📘 Book Cover Design Brief – “Growing the Ironclad Young Contender”

Project Title:
Design a bold, inspiring book cover for a best-selling book titled:
Growing the Ironclad Young Contender
Subtitle: A Family Playbook for Nurturing Bold, Grounded, and Resilient Daughters at Games and Beyond

🎯 Audience:

Parents of female athletes ages 14–20 who want their daughters to build confidence, strength, resilience, and long-term success both in sports and in life.

This book should feel encouraging, empowering, and credible — NOT cheesy, childish, or overly academic.

📕 Design Tone & Style:

Powerful and professional — should feel like a best-selling book from a leading performance or parenting expert

Emotionally compelling — conveys hope, resilience, strength, and possibility

Visually modern and clean — avoid anything overly busy, cliché, or childish

Heroic/aspirational tone — think transformation, leadership, strong positioning

💡 Visual Direction / Ideas (Use as Inspiration, Not Limitation):

Strong, confident teenage female athlete imagery — adaptable beyond one specific sport

Symbolic visuals — e.g. athlete standing strong, on a starting line, looking bold into the future, silhouette, or power stance

Bold typography that feels clean and modern (e.g., Proxima Nova, Montserrat, Gotham, Bebas Neue, etc.)

A title that stands out clearly when viewed as a thumbnail on Brindlemart

Color tones: Empowering, modern, and strong: think deep blues, greens, purples, or golds — avoid playful pastels or overly girly themes

Potential imagery: textured backgrounds, motion, bravery, development, strength, growth, sport/action overlays

🔥 What the Cover MUST Communicate:

✅ This is for parents who want strong, confident female athletes
✅ It’s a guidebook for personal development AND sports performance
✅ It’s about creating “IRONCLAD” confidence — physically, mentally and emotionally
✅ The message is: You can help your daughter become her strongest, most confident self

📚 Back-of-Book Summary (for context):

"Growing the Ironclad Young Contender" is a parent's blueprint to building girls who are strong in body, confident in mind, and ready to lead on and off the field. Through simple strategies around strength training, mindset, nutrition, and character development, this book gives parents the tools to help their daughters stay injury-resistant, break through mental barriers, and unlock their full potential — in sports and in life.

✅ Deliverables:

Full cover design (front, back, spine) for paperback
High-resolution files (print-ready)
Source files (PSD, AI, etc.)
3D mockup versions of the book (standing, flat, stack)

Target Market(s)

Industry/Entity Type

Fitness

Font styles to use
Sans Serif

Colors
FFF300
FFF600
FEFA6F
FFFEC7
FFFEE8

Requirements
Must have
• Bold Font
Should not have
• I don't want an image of a female athlete. I want this to be font based.

```html
<!DOCTYPE html>
<html lang="en">
<head>
<meta charset="utf-8">
<title>Growing the Ironclad Young Contender – Book Cover</title>
<link href="https://fonts.googleapis.com/css2?family=Montserrat:wght@700;800;900&display=swap" rel="stylesheet">
<style>
  :root {
    --page-bg: #ededed;
    --cover-bg: #0c0c0c;
    --gold-deep: #a88c3f;
    --gold-light: #ece3a4;
    --white: #ffffff;
  }
  html, body {
    margin: 0;
    padding: 0;
    width: 1200px;
    height: 1200px;
    overflow: hidden;
    background: var(--page-bg);
    font-family: "Montserrat", sans-serif;
  }
  .cover {
    position: absolute;
    left: 250px;
    top: 75px;
    width: 700px;
    height: 1049px;
    background: var(--cover-bg);
    overflow: hidden;
  }
  .cover-title {
    position: absolute;
    left: 0;
    top: 0;
    width: 700px;
    height: 400px;
  }
  .cover-title text {
    font-family: "Montserrat", sans-serif;
    font-weight: 900;
  }
  .hero-art {
    position: absolute;
    left: 130px;
    top: 411px;
    width: 480px;
    height: 347px;
    background: radial-gradient(ellipse at 45% 50%, rgba(214,190,100,0.55) 0%, rgba(168,140,63,0.25) 45%, rgba(12,12,12,0) 75%);
  }
  .subtitle {
    position: absolute;
    left: 40px;
    top: 768px;
    width: 620px;
    margin: 0;
    text-align: center;
    color: var(--white);
    font-weight: 700;
    font-size: 20px;
    line-height: 26px;
    letter-spacing: 0.3px;
    text-transform: uppercase;
  }
  .imprint {
    position: absolute;
    left: 0;
    top: 885px;
    width: 700px;
    text-align: center;
  }
  .imprint-circle {
    display: block;
    width: 72px;
    height: 72px;
    margin: 0 auto 14px;
    border: 3px solid var(--gold-deep);
    border-radius: 50%;
    box-sizing: border-box;
  }
  .imprint-name {
    color: var(--white);
    font-weight: 800;
    font-size: 24px;
    letter-spacing: 1px;
  }
</style>
</head>
<body>
  <div class="cover">
    <svg class="cover-title" viewBox="0 0 700 400" aria-label="Growing the Ironclad Young Contender">
      <defs>
        <linearGradient id="goldFoil" x1="63" y1="0" x2="635" y2="0" gradientUnits="userSpaceOnUse">
          <stop offset="0" stop-color="var(--gold-deep)"/>
          <stop offset="0.55" stop-color="var(--gold-light)"/>
          <stop offset="1" stop-color="var(--gold-deep)"/>
        </linearGradient>
      </defs>
      <text x="63" y="112" font-size="78" textLength="572" lengthAdjust="spacingAndGlyphs" fill="url(#goldFoil)">GROWING THE</text>
      <text x="63" y="186" font-size="88" textLength="572" lengthAdjust="spacingAndGlyphs" fill="#ffffff">IRONCLAD</text>
      <text x="63" y="295" font-size="138" textLength="572" lengthAdjust="spacingAndGlyphs" fill="url(#goldFoil)">YOUNG</text>
      <text x="63" y="375" font-size="92" textLength="572" lengthAdjust="spacingAndGlyphs" fill="url(#goldFoil)">CONTENDER</text>
    </svg>

    <div class="hero-art" role="img" aria-label="Gold scribble-line illustration of a young female athlete sprinting with motion streaks"></div>

    <p class="subtitle">A Family Playbook for Nurturing Bold,<br>Grounded, and Resilient Daughters<br>at Games and Beyond</p>

    <div class="imprint">
      <span class="imprint-circle"></span>
      <span class="imprint-name">IRONCLAD</span>
    </div>
  </div>
</body>
</html>
```